flat authentication

design an authentication plate and an authentication certificate

on both you need the Brix vintage store logo
authentication plate size 10 * 7cm
color black transparent text
aluminum plate material
American vintage spirit in the years 1950 to 1960

an authentication certificate
page size 4
the text to put above is in the word file
color black white red blue golden
on the certificate I would like the round golden pastille (like a seal)

```html
<!DOCTYPE html>
<html lang="en">
<head>
<meta charset="utf-8">
<title>Certificate of Authenticity</title>
<link rel="stylesheet" href="https://fonts.googleapis.com/css2?family=Oswald:wght@500;600&family=Open+Sans:wght@400&display=swap">
<style>
  :root {
    --paper: #fdfaf1;
    --navy: #12394a;
    --red: #a72b32;
    --cream: #fbe9c8;
    --ink: #111111;
    --title: #414141;
    --ribbon: #f1c9c5;
    --hatch: #d9d7d1;
    --gold-light: #f7d77a;
    --gold-dark: #c58a1b;
    --map: #f3f0e6;
  }
  html, body { margin: 0; padding: 0; overflow: hidden; }
  body { width: 1200px; height: 836px; background: #ffffff; }
  .certificate {
    position: relative;
    width: 1200px;
    height: 836px;
    background: var(--paper);
    overflow: hidden;
    font-family: "Open Sans", sans-serif;
    color: var(--ink);
  }
  .layer { position: absolute; left: 0; top: 0; }
  .map-backdrop {
    position: absolute; left: 90px; top: 200px; width: 1020px; height: 520px;
    background: var(--map); border-radius: 40px; opacity: .7;
  }
  .side-hatch {
    position: absolute; top: 205px; width: 58px; height: 560px;
    background: var(--hatch); opacity: .6;
  }
  .side-hatch--left { left: 4px; }
  .side-hatch--right { left: 1130px; }
  .title {
    position: absolute; left: 0; width: 1180px; top: 196px; margin: 0;
    text-align: center; font-family: "Oswald", sans-serif; font-weight: 600;
    font-size: 86px; line-height: 1; letter-spacing: 2px; color: var(--title);
  }
  .subtitle {
    position: absolute; left: 0; width: 1196px; top: 281px; margin: 0;
    text-align: center; font-family: "Oswald", sans-serif; font-weight: 500;
    font-size: 21px; letter-spacing: 2.5px; color: var(--title);
  }
  .statement {
    position: absolute; left: 0; width: 1184px; top: 327px; margin: 0;
    text-align: center; font-size: 17px; line-height: 25px;
  }
  .details { position: absolute; left: 327px; top: 393px; margin: 0; padding: 0; list-style: none; }
  .details li { font-size: 24px; line-height: 43.5px; white-space: pre; }
  .signature {
    position: absolute; left: 800px; top: 627px; font-size: 16px;
    display: flex; align-items: flex-end;
  }
  .signature__line { display: inline-block; width: 170px; border-bottom: 1px solid var(--ink); margin-left: 2px; height: 18px; }
</style>
</head>
<body>
<main class="certificate">
  <div class="map-backdrop" role="img" aria-label="Faint outline map of the United States"></div>
  <div class="side-hatch side-hatch--left" role="img" aria-label="Grey diagonal stripe border"></div>
  <div class="side-hatch side-hatch--right" role="img" aria-label="Grey diagonal stripe border"></div>

  <svg class="layer" width="1200" height="836" viewBox="0 0 1200 836" aria-hidden="true">
    <defs>
      <linearGradient id="flagTones" x1="0" y1="0" x2="1" y2="0">
        <stop offset="0" stop-color="#a72b32"/>
        <stop offset=".3" stop-color="#12394a"/>
        <stop offset=".55" stop-color="#a72b32"/>
        <stop offset=".8" stop-color="#12394a"/>
        <stop offset="1" stop-color="#a72b32"/>
      </linearGradient>
      <radialGradient id="goldSeal" cx=".4" cy=".35" r=".7">
        <stop offset="0" stop-color="#f7d77a"/>
        <stop offset=".6" stop-color="#e2ab38"/>
        <stop offset="1" stop-color="#c58a1b"/>
      </radialGradient>
    </defs>

    <!-- top stripes -->
    <path role="img" aria-label="Wavy red, cream and navy flag stripes"
          d="M0 0 H1200 V165 Q600 120 0 170 Z" fill="url(#flagTones)"/>
    <!-- top band -->
    <path d="M0 170 Q600 120 1200 165 V205 Q600 160 0 212 Z" fill="var(--navy)"/>
    <path d="M0 212 Q600 160 1200 205 V210 Q600 166 0 217 Z" fill="#ffffff"/>

    <!-- title ribbon -->
    <polygon fill="var(--ribbon)" opacity=".85"
             points="255,190 350,190 350,185 835,185 835,190 905,190 885,228 905,266 820,266 820,270 365,270 365,266 270,266 290,228"/>

    <!-- bottom stripes and band -->
    <path role="img" aria-label="Wavy red, cream and navy flag stripes"
          d="M0 790 Q600 660 1200 785 V836 H0 Z" fill="url(#flagTones)"/>
    <path d="M0 752 Q600 615 1200 752 V790 Q600 668 0 790 Z" fill="var(--navy)"/>
    <path d="M0 746 Q600 609 1200 746 V752 Q600 615 0 752 Z" fill="#ffffff"/>

    <!-- golden seal -->
    <circle cx="592" cy="680" r="73" fill="url(#goldSeal)"/>
    <circle cx="592" cy="680" r="56" fill="none" stroke="var(--gold-light)" stroke-width="3"/>
  </svg>

  <h1 class="title">CERTIFICATE</h1>
  <p class="subtitle">OF AUTHENTICITY</p>
  <p class="statement">This Certificate attest to the fact this original gas pump is genuine<br>and was restored by our craftsman.</p>

  <ul class="details">
    <li>Product:   xxxx</li>
    <li>Origin of the product: xxxxx</li>
    <li>Model: xxxxxx</li>
    <li>Restoration Number:   xxx      Year: xxxx</li>
    <li>Restored in Belgium by our craftsman: xxxx</li>
  </ul>

  <div class="signature">Autorised signature:<span class="signature__line"></span></div>
</main>
</body>
</html>
```